Social Media App Needs PPT Template

We need a PowerPoint template for a new social media company based in the DC area called "Bold Ledger." We provide an interactive digital platform for executives to share actionable advice. We would like to see designs that use our orange logo color as an accent, but are mainly grey, white, and black. The final design should communicate clean, chic, modern, and professional.

Target Market(s)

Executives

Industry/Entity Type

Information Technology

Font styles to use
Sans Serif

Colors
f78f20
fbe7d2
ffffff
000000
e8e8e8
757575

Requirements
Must have
• My project must have title page and many options for the body of the ppt (graphs, tables, etc). It also needs to be easy to modify. I must have someone who is experienced in creating powerpoint templates.
Nice to have
• It would be nice to have a very modern and clean design that includes the logo on every page, but still leaves a lot of room for the content of the slide
Should not have
• My design project should not look to busy.

```html
<!DOCTYPE html>
<html lang="en">
<head>
<meta charset="utf-8">
<title>Bold Ledger – Transition Page</title>
<link href="https://fonts.googleapis.com/css2?family=Lato:wght@100;300;400&display=swap" rel="stylesheet">
<style>
  :root {
    --stage-grey: #919191;
    --slide-light: #545253;
    --slide-mid: #3a3738;
    --slide-dark: #221f20;
    --band-black: #000000;
    --band-shadow: #2b2728;
    --accent-orange: #f0901b;
    --label-white: #ffffff;
    --placeholder-grey: #5e5c5d;
  }
  html, body {
    margin: 0;
    padding: 0;
    width: 1200px;
    height: 960px;
    overflow: hidden;
    background: var(--stage-grey);
    font-family: "Lato", sans-serif;
  }
  .stage {
    position: relative;
    width: 1200px;
    height: 960px;
  }
  .page-label {
    position: absolute;
    top: 46px;
    left: 0;
    width: 1200px;
    text-align: center;
    margin: 0;
    font-weight: 300;
    font-size: 24px;
    color: var(--label-white);
    letter-spacing: 0.5px;
  }
  .slide {
    position: absolute;
    left: 68px;
    top: 106px;
    width: 1062px;
    height: 797px;
    overflow: hidden;
    background: var(--slide-dark);
  }
  .slide-image {
    position: absolute;
    inset: 0;
    background: radial-gradient(ellipse 620px 560px at 600px 226px,
      var(--slide-light) 0%, var(--slide-mid) 50%, var(--slide-dark) 100%);
  }
  .image-placeholder-text {
    position: absolute;
    left: 0;
    width: 1062px;
    top: 404px;
    margin: 0;
    text-align: center;
    font-weight: 100;
    font-size: 80px;
    line-height: 1;
    color: transparent;
    -webkit-text-stroke: 1px var(--placeholder-grey);
  }
  .title-band {
    position: absolute;
    left: 0;
    top: 0;
    width: 1062px;
    height: 797px;
  }
  .section-title {
    position: absolute;
    right: 90px;
    top: 656px;
    margin: 0;
    font-weight: 400;
    font-size: 67px;
    line-height: 1;
    color: var(--label-white);
    white-space: nowrap;
  }
</style>
</head>
<body>
  <main class="stage">
    <p class="page-label">Page 2</p>
    <section class="slide">
      <div class="slide-image" role="img" aria-label="Full-bleed section image area"></div>
      <p class="image-placeholder-text">Image Goes Here</p>
      <svg class="title-band" viewBox="0 0 1062 797" aria-hidden="true">
        <polygon points="468,629 1062,629 1062,754 338,754" fill="var(--band-shadow)"/>
        <polygon points="481,629 1062,629 1062,754 348,754" fill="var(--band-black)"/>
        <polygon points="436,629 468,629 338,754 302,754" fill="var(--accent-orange)"/>
      </svg>
      <h1 class="section-title">Transition Page</h1>
    </section>
  </main>
</body>
</html>
```